we need a design for Water Bottle Lable Wrap
The product is called Calmora Springs is a restructured water. its a very healthy and rejuvenating water
we were looking at using as a tag ling Restore, Recover, Rejuvenate.

```html
<!DOCTYPE html>
<html lang="en">
<head>
<meta charset="utf-8">
<title>Calmora Springs — Bottle Label Wrap</title>
<link rel="stylesheet" href="https://fonts.googleapis.com/css2?family=Montserrat:wght@500;600&display=swap">
<style>
  :root {
    --page-bg: #ffffff;
    --label-top: #f1f9fd;
    --label-bottom: #86c2ec;
    --ink: #4a5274;
    --accent: #5fdcfb;
    --water-deep: #5f9ad6;
    --water-mid: #7cbbe8;
    --water-light: #d4edfb;
    --water-base: #8cc6ee;
  }
  * { margin: 0; padding: 0; box-sizing: border-box; }
  html, body {
    width: 1200px;
    height: 2227px;
    overflow: hidden;
    background: var(--page-bg);
  }
  .canvas {
    position: relative;
    width: 1200px;
    height: 2227px;
  }
  .label-wrap {
    position: absolute;
    left: 122px;
    top: 680px;
    width: 956px;
    height: 866px;
    border-radius: 44px;
    overflow: hidden;
    background: linear-gradient(180deg, var(--label-top) 0%, #eaf6fd 45%, var(--label-bottom) 100%);
  }
  .water-splash {
    position: absolute;
    left: 0;
    top: 290px;
    width: 956px;
    height: 576px;
    display: block;
  }
  .brand {
    position: absolute;
    left: 0;
    right: 0;
    top: 130px;
    display: flex;
    align-items: center;
    justify-content: center;
    gap: 28px;
  }
  .brand-dot {
    width: 92px;
    height: 92px;
    border-radius: 50%;
    background: var(--accent);
    flex: none;
  }
  .brand-name {
    font-family: "Montserrat", sans-serif;
    font-weight: 600;
    font-size: 74px;
    line-height: 1;
    letter-spacing: -0.01em;
    color: var(--ink);
    white-space: nowrap;
  }
  .tagline {
    position: absolute;
    left: 0;
    right: 0;
    top: 716px;
    text-align: center;
    font-family: "Montserrat", sans-serif;
    font-weight: 500;
    font-size: 31px;
    line-height: 46px;
    letter-spacing: 0.2em;
    color: var(--ink);
    text-transform: uppercase;
  }
</style>
</head>
<body>
  <main class="canvas">
    <section class="label-wrap">
      <svg class="water-splash" viewBox="0 0 956 576" role="img" aria-label="Illustration of a splashing blue water wave with droplets">
        <defs>
          <linearGradient id="waterFill" x1="0" y1="0" x2="0" y2="1">
            <stop offset="0" stop-color="var(--water-deep)"/>
            <stop offset="0.3" stop-color="var(--water-mid)"/>
            <stop offset="0.58" stop-color="var(--water-light)"/>
            <stop offset="1" stop-color="var(--water-base)"/>
          </linearGradient>
        </defs>
        <path d="M0 200 C 230 70, 560 30, 956 230 L956 576 L0 576 Z" fill="url(#waterFill)"/>
      </svg>
      <div class="brand">
        <span class="brand-dot"></span>
        <span class="brand-name">Calmora Springs</span>
      </div>
      <p class="tagline">Restore, Recover<br>Rejuvenate</p>
    </section>
  </main>
</body>
</html>
```